indépendant en tant que Massothérapeute et Préparateur Mental, j'ai besoin de ...

Massothérapeute et préparateur mental indépendant, je recherche une carte de visite sobre et dynamique, sans images liées au massage ou à la préparation mentale mais intégrant mon logo. Les couleurs que j'aime bien sont : Blanc, gris, anthracite, noir et jaune

Contact Information for Business Card

carte de préférence Horizontale
neutre qui puisse toucher le deux domaines Massothérapie et préparation mentale

Requirements
Must have
• mon projet doit intégrer au recto:
LOGO
Loïc Bardèze
078 513 26 48
info@loicbardeze.ch
et éventuellement www.loicbardeze.ch

et au verso les deux adresses:

Chemin des Ormilles 7B
1400 Yverdon-les-Bains

Route de la Gravière 9
1700 Fribourg

Should not have
• mon projet ne doit pas contenir d'image en liens avec le massage ni la préparation mentale.

```html
<!DOCTYPE html>
<html lang="fr">
<head>
<meta charset="utf-8">
<title>Loïc Bardèze – Cartes de visite</title>
<link rel="stylesheet" href="https://fonts.googleapis.com/css2?family=Lato:wght@400;700&family=Montserrat:wght@500&family=Oswald:wght@600&display=swap">
<style>
  :root {
    --bg: #1a1a1a;
    --card: #2f2f30;
    --card-dark: #28282a;
    --white: #ffffff;
    --grey: #d9d9d9;
    --yellow: #f2b705;
  }
  * { margin: 0; padding: 0; box-sizing: border-box; }
  html, body { width: 1200px; height: 896px; overflow: hidden; background: var(--bg); }
  .canvas {
    width: 1200px; height: 896px;
    display: flex; flex-direction: column; align-items: center; justify-content: center; gap: 48px;
  }
  .card {
    position: relative;
    width: 660px; height: 377px;
    background: linear-gradient(135deg, var(--card) 0%, var(--card-dark) 100%);
    border-bottom: 7px solid var(--yellow);
    box-shadow: 0 14px 30px rgba(0,0,0,.55);
    color: var(--white);
    font-family: "Lato", sans-serif;
  }
  .brand {
    position: absolute; left: 150px; top: 92px;
    display: flex; align-items: center; gap: 18px;
  }
  .brand-square { width: 38px; height: 38px; background: var(--white); }
  .brand-name { font-family: "Lato", sans-serif; font-weight: 700; font-size: 36px; line-height: 1; color: var(--white); }
  .brand-tagline {
    font-family: "Montserrat", sans-serif; font-weight: 500;
    font-size: 9.5px; letter-spacing: .12em; text-transform: uppercase;
    color: var(--white); margin-top: 6px;
  }
  .addresses {
    position: absolute; left: 150px; top: 200px;
    list-style: none; display: flex; flex-direction: column; gap: 16px;
    font-size: 17px;
  }
  .addresses li, .contacts li { display: flex; align-items: center; gap: 10px; }
  .icon { width: 14px; height: 14px; flex: none; }
  .identity {
    position: absolute; left: 150px; top: 228px;
    display: flex; align-items: center; gap: 26px;
  }
  .person-name { font-family: "Oswald", sans-serif; font-weight: 600; font-size: 26px; text-transform: uppercase; letter-spacing: .01em; line-height: 1.1; }
  .person-role { font-size: 17px; color: var(--grey); }
  .divider { width: 1px; height: 72px; background: var(--yellow); }
  .contacts { list-style: none; display: flex; flex-direction: column; gap: 8px; font-size: 16px; }
</style>
</head>
<body>
<main class="canvas">

  <section class="card card-back" aria-label="Verso : adresses">
    <div class="brand">
      <span class="brand-square"></span>
      <div>
        <div class="brand-name">Loïc Bardèze</div>
        <div class="brand-tagline">Massothérapeute / Préparateur mental</div>
      </div>
    </div>
    <ul class="addresses">
      <li>
        <svg class="icon" viewBox="0 0 14 14" aria-hidden="true"><path d="M7 1a4 4 0 0 0-4 4c0 3 4 8 4 8s4-5 4-8a4 4 0 0 0-4-4z" fill="var(--yellow)"/><circle cx="7" cy="5" r="1.5" fill="var(--card)"/></svg>
        Chemin des Ormilles 7B, 1400 Yverdon-les-Bains
      </li>
      <li>
        <svg class="icon" viewBox="0 0 14 14" aria-hidden="true"><path d="M7 1a4 4 0 0 0-4 4c0 3 4 8 4 8s4-5 4-8a4 4 0 0 0-4-4z" fill="var(--yellow)"/><circle cx="7" cy="5" r="1.5" fill="var(--card)"/></svg>
        Route de la Gravière 9, 1700 Freiburg
      </li>
    </ul>
  </section>

  <section class="card card-front" aria-label="Recto : contact">
    <div class="brand">
      <span class="brand-square"></span>
      <div>
        <div class="brand-name">Loïc Bardèze</div>
        <div class="brand-tagline">Massothérapeute / Préparateur mental</div>
      </div>
    </div>
    <div class="identity">
      <div>
        <div class="person-name">Loïc Bardèze</div>
        <div class="person-role">Founder &amp; CEO</div>
      </div>
      <span class="divider"></span>
      <ul class="contacts">
        <li>
          <svg class="icon" viewBox="0 0 14 14" aria-hidden="true"><path d="M3 1.5l2.2 0 1 3-1.4 1a7 7 0 0 0 3.7 3.7l1-1.4 3 1v2.2a1 1 0 0 1-1 1A10.5 10.5 0 0 1 2 2.5a1 1 0 0 1 1-1z" fill="var(--yellow)"/></svg>
          078 513 26 48
        </li>
        <li>
          <svg class="icon" viewBox="0 0 14 14" aria-hidden="true"><rect x="1" y="3" width="12" height="8.5" fill="var(--yellow)"/><path d="M1 3l6 5 6-5" fill="none" stroke="var(--card)" stroke-width="1.2"/></svg>
          info@loicbardeze.ch
        </li>
        <li>
          <svg class="icon" viewBox="0 0 14 14" aria-hidden="true"><circle cx="7" cy="7" r="5.8" fill="var(--yellow)"/><path d="M1.2 7h11.6M7 1.2c-2.4 3-2.4 8.6 0 11.6M7 1.2c2.4 3 2.4 8.6 0 11.6" fill="none" stroke="var(--card)" stroke-width="1"/></svg>
          www.loicbardeze.ch
        </li>
      </ul>
    </div>
  </section>

</main>
</body>
</html>
```